Naturopath Practitioner Card Design

I am a naturopath needing a design for a business card mainly to show that I am a naturopath and have some contact details to give to prospective clients. I am open minded about the design and what is on the second side of the card whether it just be some artwork or space for details, appointment times etc. Naturopathy is the practice of natural medicine that uses a holistic approach and incorporates herbal and nutritional medicine.

Industry/Entity Type

Business

Contact Information for Business Card

Tom Rudd NaturopathBHSc (Naturopathy) Member WHPG 0487 925 316 tom.rudd@mailexample.com www.tomruddnaturopathy.example.au

Requirements
Nice to have
• Would prefer some kind of original pattern/art work/logo rather than an image, not fussed if its very simple/basic
• I am open to any colour but think I would prefer a more earthy sandy clay etc type style than the greens that are commonly associated with naturopathy.
Should not have
• Don't really want to have generic stock images on it

```html
<!DOCTYPE html>
<html lang="en">
<head>
<meta charset="utf-8">
<title>Tom Rudd Naturopathy – Business Card</title>
<link rel="stylesheet" href="https://fonts.googleapis.com/css2?family=Cinzel:wght@400&family=Open+Sans:wght@400;700&display=swap">
<style>
  :root {
    --page-bg: #ebe7e0;
    --card-white: #ffffff;
    --brand-green: #728c40;
    --brand-green-text: #6a8a34;
    --ink-dark: #333333;
    --ink-body: #3a3a3a;
    --rule: #c9c9c9;
  }
  * { box-sizing: border-box; margin: 0; padding: 0; }
  html, body {
    width: 1200px;
    height: 1000px;
    overflow: hidden;
    background: var(--page-bg);
  }
  .card {
    position: absolute;
    left: 265px;
    width: 666px;
    height: 397px;
    box-shadow: 0 3px 10px rgba(0,0,0,0.18);
    text-align: center;
  }
  .card--front { top: 73px; background: var(--card-white); }
  .card--back { top: 532px; background: var(--brand-green); color: var(--card-white); }

  .brand-dot {
    position: absolute;
    left: 50%;
    width: 64px;
    height: 64px;
    margin-left: -32px;
    border-radius: 50%;
  }
  .card--front .brand-dot { top: 52px; background: var(--brand-green); }
  .card--back .brand-dot { top: 58px; background: var(--card-white); }

  .brand-name {
    position: absolute;
    left: 0;
    right: 0;
    font-family: "Cinzel", serif;
    font-weight: 400;
    line-height: 1;
  }
  .brand-name__main { display: block; font-size: 54px; letter-spacing: 1px; }
  .brand-name__sub { display: block; font-size: 24px; letter-spacing: 1.5px; margin-top: 10px; }
  .card--front .brand-name { top: 156px; color: var(--ink-dark); }
  .card--back .brand-name { top: 168px; color: var(--card-white); }

  .practitioner {
    position: absolute;
    top: 268px;
    left: 0;
    right: 0;
    font-family: "Open Sans", sans-serif;
    color: var(--brand-green-text);
    font-size: 17px;
  }
  .practitioner__name { font-weight: 700; font-size: 19px; }
  .practitioner__rule {
    width: 240px;
    height: 1px;
    margin: 5px auto 0;
    background: linear-gradient(90deg, transparent, var(--rule), transparent);
  }
  .membership {
    position: absolute;
    top: 300px;
    left: 0;
    right: 0;
    font-family: "Open Sans", sans-serif;
    font-size: 15px;
    color: var(--ink-body);
  }
  .contacts {
    position: absolute;
    top: 337px;
    left: 0;
    right: 0;
    display: flex;
    justify-content: center;
    gap: 16px;
    font-family: "Open Sans", sans-serif;
    font-size: 15px;
    color: var(--ink-body);
  }
  .contact { display: flex; align-items: center; gap: 5px; white-space: nowrap; }
  .contact svg { width: 14px; height: 14px; fill: var(--brand-green); }
  .band {
    position: absolute;
    left: 0;
    right: 0;
    bottom: 0;
    height: 25px;
    background: var(--brand-green);
  }
</style>
</head>
<body>

<section class="card card--front" aria-label="Card front">
  <div class="brand-dot"></div>
  <div class="brand-name">
    <span class="brand-name__main">Tom Rudd</span>
    <span class="brand-name__sub">Naturopathy</span>
  </div>
  <div class="practitioner">
    <span class="practitioner__name">Tom Rudd</span> BHSc (Naturopathy)
    <div class="practitioner__rule"></div>
  </div>
  <p class="membership">Member WHPG</p>
  <div class="contacts">
    <span class="contact">
      <svg viewBox="0 0 16 16" aria-hidden="true"><path d="M1 3h14v10H1z" /><path d="M1 3l7 6 7-6" fill="none" stroke="#fff" stroke-width="1.4"/></svg>
      tom.rudd@mailexample.com
    </span>
    <span class="contact">
      <svg viewBox="0 0 16 16" aria-hidden="true"><path d="M3.5 1l2.5 3-1.5 1.8c.8 1.8 2.1 3.2 3.9 4.1L10.2 8.4l3.3 2.3-1 3.3C7 13.6 2.4 9 2 3.2z"/></svg>
      0487 925 316
    </span>
    <span class="contact">
      <svg viewBox="0 0 16 16" aria-hidden="true"><circle cx="8" cy="8" r="7"/><path d="M1 8h14M8 1c-3 3.5-3 10.5 0 14M8 1c3 3.5 3 10.5 0 14" fill="none" stroke="#fff" stroke-width="1"/></svg>
      www.tomruddnaturopathy.example.au
    </span>
  </div>
  <div class="band"></div>
</section>

<section class="card card--back" aria-label="Card back">
  <div class="brand-dot"></div>
  <div class="brand-name">
    <span class="brand-name__main">Tom Rudd</span>
    <span class="brand-name__sub">Naturopathy</span>
  </div>
</section>

</body>
</html>
```